BrindleStaffing Business Card Design

We are a staffing company finding positions for dedicated nurses and physicians.

Target Market(s)

Business Professionals

Industry/Entity Type

Staffing

Contact Information for Business Card

Gordon Pratley
Chairman
417 39th Avenue South
SAINT PETERSBURG FL 33712
813-555-4172 Mobile
813-555-8036 Fax
gpratley@brindlestaffing.com
www.brindlestaffing.com

Font styles to use
Sans Serif

Colors
fbee3e
f04a50
f37122

Requirements
Must have
• Logo Attached, see colors below. We'd like to see Yellow, Orange and Red.

```html
<!DOCTYPE html>
<html lang="en">
<head>
<meta charset="utf-8">
<title>BrindleStaffing Business Card</title>
<link href="https://fonts.googleapis.com/css2?family=Open+Sans:wght@400;600;700&display=swap" rel="stylesheet">
<style>
  :root {
    --brand-orange: #f37122;
    --brand-orange-deep: #e0621a;
    --brand-red: #f04a50;
    --brand-yellow: #fbee3e;
    --paper: #ffffff;
    --ink: #1d1d1f;
    --backdrop: #e4e4e6;
  }
  * { box-sizing: border-box; margin: 0; padding: 0; }
  html, body { width: 1200px; height: 1200px; overflow: hidden; }
  body {
    background: var(--backdrop);
    font-family: "Open Sans", Arial, sans-serif;
    position: relative;
  }
  .card {
    position: absolute;
    left: 236px;
    width: 733px;
    height: 440px;
    background: var(--paper);
    overflow: hidden;
  }
  .card--front { top: 110px; }
  .card--back { top: 642px; }

  .front-header {
    position: absolute; left: 0; top: 0;
    width: 100%; height: 232px;
    background: var(--brand-orange);
  }
  .header-block {
    position: absolute; left: 568px; top: 71px;
    width: 94px; height: 94px;
    background: var(--brand-orange-deep);
  }
  .holder-name {
    position: absolute; left: 37px; top: 92px;
    color: var(--paper);
    font-size: 38px; font-weight: 400; line-height: 46px;
    letter-spacing: 0.2px;
  }
  .holder-title {
    position: absolute; left: 39px; top: 140px;
    color: var(--paper);
    font-size: 17px; font-weight: 400; line-height: 22px;
    letter-spacing: 0.5px;
  }
  .accent-rule {
    position: absolute; left: 0; width: 100%; height: 8px;
    background: var(--brand-yellow);
  }
  .front-header + .accent-rule { top: 232px; }

  .contact-list {
    position: absolute; left: 36px; top: 256px;
    list-style: none;
    color: var(--ink);
    font-size: 17px; line-height: 22px;
  }
  .contact-item {
    display: flex; align-items: flex-start;
    margin-bottom: 8px;
  }
  .contact-icon {
    width: 17px; height: 17px; flex: none;
    margin-right: 10px; margin-top: 2px;
    fill: var(--brand-red);
  }
  .contact-label { color: var(--brand-red); font-weight: 600; margin-left: 6px; }
  .contact-item--address { line-height: 22.5px; }

  .brand-wordmark {
    position: absolute; left: 0; right: 0; top: 160px;
    text-align: center;
    color: var(--brand-red);
    font-size: 62px; font-weight: 700;
    letter-spacing: -1px;
  }
  .back-footer {
    position: absolute; left: 0; top: 378px;
    width: 100%; height: 62px;
    background: var(--brand-orange);
  }
  .card--back .accent-rule { top: 370px; }
</style>
</head>
<body>
  <section class="card card--front" aria-label="Business card front">
    <div class="front-header">
      <div class="header-block"></div>
      <h1 class="holder-name">Gordon Pratley</h1>
      <p class="holder-title">Chairman</p>
    </div>
    <div class="accent-rule"></div>
    <ul class="contact-list">
      <li class="contact-item">
        <svg class="contact-icon" viewBox="0 0 24 24" aria-hidden="true"><path d="M6.6 10.8a15.1 15.1 0 0 0 6.6 6.6l2.2-2.2a1 1 0 0 1 1-.25 11.4 11.4 0 0 0 3.6.57 1 1 0 0 1 1 1V20a1 1 0 0 1-1 1A17 17 0 0 1 3 4a1 1 0 0 1 1-1h3.5a1 1 0 0 1 1 1c0 1.25.2 2.45.57 3.57a1 1 0 0 1-.25 1z"/></svg>
        <span>813-555-4172<span class="contact-label">Mobile</span></span>
      </li>
      <li class="contact-item">
        <svg class="contact-icon" viewBox="0 0 24 24" aria-hidden="true"><path d="M2 5h20v14H2z"/><path d="M3 6l9 7 9-7" fill="none" stroke="#fff" stroke-width="1.5"/></svg>
        <span>gpratley@brindlestaffing.com</span>
      </li>
      <li class="contact-item">
        <svg class="contact-icon" viewBox="0 0 24 24" aria-hidden="true"><g fill="none" stroke="var(--brand-red)" stroke-width="1.8"><circle cx="12" cy="12" r="9.5"/><ellipse cx="12" cy="12" rx="4" ry="9.5"/><path d="M2.5 12h19M4 7h16M4 17h16"/></g></svg>
        <span>www.brindlestaffing.com</span>
      </li>
      <li class="contact-item contact-item--address">
        <svg class="contact-icon" viewBox="0 0 24 24" aria-hidden="true"><path d="M12 1.5a7.5 7.5 0 0 0-7.5 7.5c0 5.6 7.5 13.5 7.5 13.5s7.5-7.9 7.5-13.5A7.5 7.5 0 0 0 12 1.5zm0 10.2a2.7 2.7 0 1 1 0-5.4 2.7 2.7 0 0 1 0 5.4z"/></svg>
        <span>417 39th Avenue South<br>SAINT PETERSBURG FL 33712<br>813-555-8036<span class="contact-label">Fax</span></span>
      </li>
    </ul>
  </section>

  <section class="card card--back" aria-label="Business card back">
    <p class="brand-wordmark">BrindleStaffing</p>
    <div class="accent-rule"></div>
    <div class="back-footer"></div>
  </section>
</body>
</html>
```